New Fun, Positive, energised looking Business Card Needed for High Achiever Coach

I am looking for a two sided full colour business card. I am self employed and have recently re branded my 1-2-1 work re-vitalising high achievers. My target client base for these cards is therefore high achievers - usually aged 40 -55, they are often entrepreneurs, CEO or work in banking and finance and 2/3 are male. I work with them on 90 day or 6 month coaching programs to help them live their success in a healthier, more sustainable and fulfiiled way. They pay for this privately so though they are corporate types the cards need not look 'corporate'. I want to portray the idea of transformation, vitality and re-connecting.
You can get a feel for the look I like on my new website: morvenlisk.co.uk
I want to use this logo with strapline (Re-Vitalising High Achievers) (I purchased off Logoharbor) and font/ colours (the turquoise and green).
Details to include on the card:
www.morvenlisk.co.uk
+44 7915 302618
morven@morvenlisk.co.uk
skype: morvenlisk
I'd also like to include:
Do you struggle to switch off? Want to be healthier and feel fitter? Want closer relationships? More clarity over the direction you are headed? I can help you do these things using integrated mind-body techniques. Visit morvenlisk.co.uk TODAY to apply for a FREE Breakthrough session.
BUT if that is too much text for a card I am open to advice/ammendments.
Updates
Thanks for your design - I am considering them. PLease change the wording to :

```html
<!DOCTYPE html>
<html lang="en">
<head>
<meta charset="utf-8">
<title>Morven Lisk – Business Card</title>
<link rel="stylesheet" href="https://fonts.googleapis.com/css2?family=Tinos:wght@400;700&family=Open+Sans:wght@400;700&display=swap">
<style>
  :root {
    --turquoise: #00a6ca;
    --green: #5fb862;
    --white: #ffffff;
    --ink: #2e3236;
    --ink-soft: #3a4a52;
    --divider: #c9cfd3;
    --backdrop: #eceef2;
  }
  * { box-sizing: border-box; margin: 0; padding: 0; }
  html, body {
    width: 1200px;
    height: 987px;
    overflow: hidden;
    background: var(--backdrop);
  }
  .card {
    position: absolute;
    left: 220px;
    width: 760px;
    height: 434px;
    border-radius: 34px;
    overflow: hidden;
    box-shadow: 0 6px 18px rgba(0,0,0,0.12);
  }
  .card--front { top: 42px; background: var(--white); }
  .card--back  { top: 511px; background: var(--turquoise); }

  .front-shapes { position: absolute; inset: 0; }

  .brand-block {
    position: absolute;
    left: 44px;
    top: 48px;
    width: 340px;
  }
  .brand-dot {
    display: block;
    width: 86px;
    height: 86px;
    margin-left: 120px;
    border-radius: 50%;
    background: var(--green);
  }
  .brand-name {
    margin-top: 14px;
    font-family: "Tinos", serif;
    font-weight: 700;
    font-size: 56px;
    line-height: 1;
    color: var(--turquoise);
  }
  .strapline {
    margin-top: 8px;
    font-family: "Tinos", serif;
    font-weight: 400;
    font-size: 24px;
    color: var(--turquoise);
  }
  .phone {
    position: absolute;
    right: 26px;
    top: 58px;
    font-family: "Tinos", serif;
    font-weight: 700;
    font-size: 31px;
    color: var(--white);
    white-space: nowrap;
  }
  .contact-list {
    position: absolute;
    left: 250px;
    top: 290px;
    padding-left: 22px;
    border-left: 1.5px solid var(--divider);
    list-style: none;
    font-family: "Tinos", serif;
    font-size: 22px;
    color: var(--ink);
  }
  .contact-list li {
    display: flex;
    align-items: center;
    gap: 10px;
    line-height: 1.5;
  }
  .contact-icon { width: 18px; height: 18px; flex: none; }

  .back-copy {
    position: absolute;
    font-family: "Open Sans", sans-serif;
    font-size: 20px;
    line-height: 1.3;
    color: var(--ink-soft);
  }
  .back-copy--question { left: 56px; top: 62px; width: 330px; }
  .back-copy--answer { left: 420px; top: 196px; width: 300px; }
  .copy-label { display: block; font-size: 17px; color: var(--ink); }
  .back-copy p + p { margin-top: 6px; }
  .highlight { color: var(--white); font-weight: 700; }
</style>
</head>
<body>

<section class="card card--front" aria-label="Business card front">
  <svg class="front-shapes" viewBox="0 0 760 434" width="760" height="434" aria-hidden="true">
    <path d="M238,0 C430,24 610,205 700,434 L760,434 L760,0 Z" fill="var(--turquoise)"/>
    <path d="M212,0 C404,28 584,212 672,434" fill="none" stroke="var(--green)" stroke-width="12"/>
  </svg>

  <div class="brand-block">
    <span class="brand-dot" aria-hidden="true"></span>
    <div class="brand-name">Morven Lisk</div>
    <div class="strapline">Re-Vitalising High Achievers</div>
  </div>

  <div class="phone">+44 7915 302618</div>

  <ul class="contact-list">
    <li>
      <svg class="contact-icon" viewBox="0 0 20 20" aria-hidden="true">
        <rect x="1" y="4" width="18" height="13" rx="2" fill="var(--turquoise)"/>
        <path d="M2,5 L10,12 L18,5" fill="none" stroke="var(--white)" stroke-width="1.6"/>
      </svg>
      morven@morvenlisk.co.uk
    </li>
    <li>
      <svg class="contact-icon" viewBox="0 0 20 20" aria-hidden="true">
        <circle cx="10" cy="10" r="8.5" fill="none" stroke="var(--turquoise)" stroke-width="1.6"/>
        <ellipse cx="10" cy="10" rx="3.6" ry="8.5" fill="none" stroke="var(--turquoise)" stroke-width="1.4"/>
        <path d="M1.5,10 H18.5 M3,5.5 H17 M3,14.5 H17" stroke="var(--turquoise)" stroke-width="1.2"/>
      </svg>
      www.morvenlisk.co.uk
    </li>
    <li>
      <svg class="contact-icon" viewBox="0 0 20 20" aria-hidden="true">
        <circle cx="10" cy="10" r="9" fill="var(--turquoise)"/>
      </svg>
      morvenlisk
    </li>
  </ul>
</section>

<section class="card card--back" aria-label="Business card back">
  <div class="back-copy back-copy--question">
    <span class="copy-label">Q</span>
    <p>Do you struggle to switch off?</p>
    <p>Want to be healthier &amp; feel fitter?</p>
    <p>Want closer relationships?</p>
    <p>More clarity over the direction you are headed?</p>
  </div>
  <div class="back-copy back-copy--answer">
    <span class="copy-label">A</span>
    <p>I can help you do these things using integrated mind-body techniques.</p>
    <p>Visit <span class="highlight">morvenlisk.co.uk</span> TODAY to apply for a FREE Breakthrough session.</p>
  </div>
</section>

</body>
</html>
```